Stationery Design Project for Marketing Consultancy

I have started a new consultancy business and require the following elements to be designed using existing logo:
• Business card
• Letterhead
• Envelope (DL, C4, C5)
• Microsoft word template for report writing
• A4 Presentation Folder
• Powerpoint template
COPY FOR FRONT AND BACK OF BUSINESS CARD
logo
'Measurable Marketing. Epic Results' slogan (but no need to use existing lockup with logo)
name, B Com, Grad Cert Brand Strategy, AMP (post nominal abbreviations in smaller font)
mobile: 04XX-XXX-XXX (I will give details to the winner to add)
website: www.tolvarin.com.au
email: info@tolvarin.com.au
COPY FOR LETTERHEAD
Logo
Company Name
Please, submit your designs that include business card, letterhead and envelope. Once selected the winner will be asked to complete the project by creating the rest of the artwork.
FINAL FILES
Print ready files to be supplied as well as Indesign files so that minor amends can be made if necessary in future.
• Layered vectors in EPS & PDF
• Screen quality JPEG & PNGs
ABOUT THE BUSINESS: TOLVARIN
I work with clients to understand their business challenges, developing and executing measurable marketing strategies tied to key business metrics. Services include:
Services include:
• Business planning and business development
• Marketing and brand strategy
• Insight-driven integrated campaigns
• Loyalty programs and retention marketing
• Marketing automation
• Direct marketing (traditional and digital)
• Content strategy and development
Hi everyone,
Target Market(s)
Corporate decision makers (heads of marketing, general managers etc) and small to medium sized business owners. Predominately male aged 35+
Industry/Entity Type
Marketing
Requirements
Must have
- BRAND PERSONALITY
The successful design will communicate brand personality. I am a professional, results-driven entrepreneur, but want to show off my creative flair.
MEMORABILITY
Looking for a unique and eye-catching design. Am considering special printing effects (die cuts, letterpress, interactive elements, embossing, foiling etc) or a striking minimalist approach.
Nice to have
- I have a mission that could be incorporated on reverse if room -
Turning insights into actions & passion into profit.
Should not have
- Use of pink or green.

```html
<!DOCTYPE html>
<html lang="en">
<head>
<meta charset="utf-8">
<title>Tolvarin Stationery</title>
<link href="https://fonts.googleapis.com/css2?family=Open+Sans:wght@400;600;700;800&display=swap" rel="stylesheet">
<style>
  :root {
    --backdrop: #e9e6e2;
    --paper: #f6f6f6;
    --ink: #1e1e1e;
    --ink-soft: #555555;
    --band-dark: #3a3a3a;
    --band-mid: #6d6d6d;
    --band-light: #bdbdbd;
    --footer-text: #f2f2f2;
  }
  * { margin: 0; padding: 0; box-sizing: border-box; }
  html, body { width: 1200px; height: 798px; overflow: hidden; }
  body {
    background: var(--backdrop);
    font-family: "Open Sans", Arial, sans-serif;
    color: var(--ink);
    position: relative;
  }
  .sheet {
    position: absolute;
    background: var(--paper);
    overflow: hidden;
    box-shadow: 0 6px 18px rgba(0,0,0,0.25);
  }
  .sheet svg.waves { position: absolute; inset: 0; width: 100%; height: 100%; }

  .brand { position: absolute; display: flex; flex-direction: column; align-items: center; }
  .brand-line { display: flex; align-items: center; gap: 4px; }
  .brand-dot { border-radius: 50%; background: var(--ink); }
  .brand-name { font-weight: 800; color: var(--ink); letter-spacing: 0.02em; line-height: 1; }
  .brand-tagline { font-weight: 700; color: var(--ink-soft); text-transform: uppercase; white-space: nowrap; line-height: 1.2; }

  .mark-area { position: absolute; }

  .footer-text { position: absolute; color: var(--footer-text); line-height: 1.35; white-space: nowrap; }
  .footer-text .company { font-weight: 600; }

  /* letterhead */
  .letterhead { left: 150px; top: 170px; width: 382px; height: 508px; }
  .letterhead .brand { right: 12px; top: 10px; }
  .letterhead .brand-dot { width: 10px; height: 10px; }
  .letterhead .brand-name { font-size: 11px; }
  .letterhead .brand-tagline { font-size: 4px; }
  .letterhead .mark-area { left: 70px; top: 170px; width: 220px; height: 170px; border-radius: 50%;
    background: radial-gradient(ellipse at center, #bdbdbd 0%, #d2d2d2 55%, rgba(246,246,246,0) 72%); }
  .letterhead .footer-text { left: 48px; bottom: 14px; font-size: 6px; }
  .letterhead .footer-text .company { font-size: 7px; }

  /* business card front */
  .card-front { left: 673px; top: 122px; width: 242px; height: 156px; }
  .card-front .brand { left: 0; right: 0; top: 44px; }
  .card-front .brand-dot { width: 16px; height: 16px; }
  .card-front .brand-name { font-size: 22px; }
  .card-front .brand-tagline { font-size: 6px; margin-top: 3px; }

  /* business card back */
  .card-back { left: 818px; top: 262px; width: 245px; height: 158px; }
  .card-back .details { position: absolute; left: 14px; top: 30px; font-size: 8px; line-height: 1.4; color: var(--ink); white-space: nowrap; }
  .card-back .details .name { font-size: 11px; font-weight: 600; }
  .card-back .details .post { font-size: 7px; }
  .card-back .details .web { font-weight: 700; }
  .card-back .brand { right: 10px; top: 96px; }
  .card-back .brand-dot { width: 8px; height: 8px; }
  .card-back .brand-name { font-size: 10px; }

  /* envelope */
  .envelope { left: 600px; top: 464px; width: 384px; height: 216px; }
  .envelope .brand { right: 10px; top: 8px; }
  .envelope .brand-dot { width: 10px; height: 10px; }
  .envelope .brand-name { font-size: 11px; }
  .envelope .brand-tagline { font-size: 4px; }
  .envelope .mark-area { left: 95px; top: 22px; width: 190px; height: 150px; border-radius: 50%;
    background: radial-gradient(ellipse at center, rgba(200,200,200,0.75) 0%, rgba(200,200,200,0.35) 50%, rgba(200,200,200,0) 72%); }
  .envelope .footer-text { left: 44px; bottom: 10px; font-size: 5.5px; }
  .envelope .footer-text .company { font-size: 6.5px; }
</style>
</head>
<body>

<section class="sheet letterhead">
  <svg class="waves" viewBox="0 0 382 508" preserveAspectRatio="none" aria-hidden="true">
    <defs>
      <linearGradient id="lh-top" x1="0" y1="0" x2="1" y2="0">
        <stop offset="0" stop-color="#9a9a9a"/><stop offset="1" stop-color="#3c3c3c"/>
      </linearGradient>
      <linearGradient id="lh-foot" x1="0" y1="0" x2="1" y2="0">
        <stop offset="0" stop-color="#2e2e2e"/><stop offset="1" stop-color="#5a5a5a"/>
      </linearGradient>
    </defs>
    <path d="M150 0 C210 22 270 28 382 14 L382 0 Z" fill="var(--band-light)"/>
    <path d="M170 0 C230 40 300 46 382 38 L382 30 C300 34 240 26 200 0 Z" fill="url(#lh-top)"/>
    <path d="M210 0 C260 30 320 36 382 30 L382 14 C300 24 250 14 230 0 Z" fill="#e0e0e0"/>
    <path d="M0 440 C90 420 200 460 382 420 L382 508 L0 508 Z" fill="var(--band-light)"/>
    <path d="M0 455 C100 430 210 470 382 432 L382 508 L0 508 Z" fill="var(--band-mid)"/>
    <path d="M0 468 C110 448 220 478 382 450 L382 508 L0 508 Z" fill="url(#lh-foot)"/>
  </svg>
  <div class="brand">
    <div class="brand-line"><span class="brand-dot"></span><span class="brand-name">TOLVARIN</span></div>
    <span class="brand-tagline">Clear Marketing. Real Growth.</span>
  </div>
  <div class="mark-area" role="img" aria-label="Faint large brand mascot illustration"></div>
  <div class="footer-text">
    <div class="company">Company Name</div>
    <div>mobile: 04XX-XXX-XXX</div>
    <div>email: info@tolvarin.com.au</div>
    <div>www.tolvarin.com.au</div>
  </div>
</section>

<section class="sheet card-front">
  <svg class="waves" viewBox="0 0 242 156" preserveAspectRatio="none" aria-hidden="true">
    <path d="M60 0 C120 14 180 6 242 26 L242 0 Z" fill="var(--band-light)"/>
    <path d="M110 0 C160 10 200 14 242 36 L242 28 C200 10 160 4 140 0 Z" fill="var(--band-mid)"/>
    <path d="M0 118 C70 106 150 132 242 114 L242 156 L0 156 Z" fill="var(--band-light)"/>
    <path d="M0 128 C80 116 160 140 242 126 L242 156 L0 156 Z" fill="var(--band-dark)"/>
  </svg>
  <div class="brand">
    <div class="brand-line"><span class="brand-dot"></span><span class="brand-name">TOLVARIN</span></div>
    <span class="brand-tagline">Clear Marketing. Real Growth.</span>
  </div>
</section>

<section class="sheet card-back">
  <svg class="waves" viewBox="0 0 245 158" preserveAspectRatio="none" aria-hidden="true">
    <path d="M90 0 C150 10 200 6 245 20 L245 0 Z" fill="var(--band-light)"/>
    <path d="M0 128 C80 116 160 142 245 124 L245 158 L0 158 Z" fill="var(--band-light)"/>
    <path d="M0 138 C90 126 170 150 245 136 L245 158 L0 158 Z" fill="var(--band-dark)"/>
  </svg>
  <div class="details">
    <div class="name">Company Name</div>
    <div>Principal</div>
    <div class="post">B Com, Grad Cert Brand Strategy, AMP</div>
    <div>mobile: 04XX-XXX-XXX</div>
    <div>email: info@tolvarin.com.au</div>
    <div class="web">www.tolvarin.com.au</div>
  </div>
  <div class="brand">
    <div class="brand-line"><span class="brand-dot"></span><span class="brand-name">TOLVARIN</span></div>
  </div>
</section>

<section class="sheet envelope">
  <svg class="waves" viewBox="0 0 384 216" preserveAspectRatio="none" aria-hidden="true">
    <defs>
      <linearGradient id="env-panel" x1="0" y1="0" x2="1" y2="0">
        <stop offset="0" stop-color="#5a5a5a"/><stop offset="1" stop-color="#3e3e3e"/>
      </linearGradient>
    </defs>
    <path d="M0 0 L170 0 L170 216 L0 216 Z" fill="url(#env-panel)"/>
    <path d="M170 0 L190 0 L190 216 L170 216 Z" fill="#9a9a9a"/>
    <path d="M130 0 C200 18 290 24 384 12 L384 0 Z" fill="var(--band-light)"/>
    <path d="M200 0 C260 26 320 34 384 30 L384 22 C320 26 270 16 240 0 Z" fill="var(--band-dark)"/>
    <path d="M0 168 C100 150 220 186 384 160 L384 216 L0 216 Z" fill="var(--band-light)"/>
    <path d="M0 180 C110 162 230 196 384 172 L384 216 L0 216 Z" fill="var(--band-mid)"/>
    <path d="M0 190 C120 176 240 204 384 184 L384 216 L0 216 Z" fill="var(--band-dark)"/>
  </svg>
  <div class="mark-area" role="img" aria-label="Faint large brand mascot illustration"></div>
  <div class="brand">
    <div class="brand-line"><span class="brand-dot"></span><span class="brand-name">TOLVARIN</span></div>
    <span class="brand-tagline">Clear Marketing. Real Growth.</span>
  </div>
  <div class="footer-text">
    <div class="company">Company Name</div>
    <div>mobile: 04XX-XXX-XXX</div>
    <div>email: info@tolvarin.com.au</div>
    <div>www.tolvarin.com.au</div>
  </div>
</section>

</body>
</html>
```